Medical Implant company needs a Top Quality Premium Brochure

We need to create a top quality brochure for VIP clients, formed by top spine surgeons. The main goal here is to cause a deep quality impact, positioning the company and it´s solutions above the others, with a refined, unique and creative material.

Special paper, hot stamping, innovative format are welcome.

For more information check out our website: www.corvalento.com.br (web translator are recommended for content understanding)

Corvalento works with top quality spine and pain management products, providing solutions for the medical specialists, investing in high quality processes and continued medical education.

Short briefing:
1 - Company profile
2 - Quality / vision
3 - Continued education programs
4 - Main products
5 - Main partners
6 - Final stuff (creative final thoughts / considerations)

FORMAT: 25 x 18,5 cm (horizontal)
PAGES - 16

REFERENCES:

https://www.folioquarry.net/gallery/52930184/Medical-Healthcare-Profile-Brochure

https://www.folioquarry.net/gallery/7719046/TK-Alpine-Style-Brochure

Target Market(s)

Mainly brazilian spine and neuro surgeons with minimally invasive surgery skills.

Industry/Entity Type

Education

Requirements
Must have

• 18 pages design

1. Cover
2. IMAGE + TITLE - About Us
3. IMAGE + TEXT - About Us
4. IMAGE + TITLE - Vision
5. IMAGE + TEXT - Vision
6. IMAGE + TITLE - Quality
7. IMAGE + TEXT - Quality
8. Timeline Left
9. Timeline Right
10. IMAGE + TITLE - Medical Education
11. IMAGE + TEXT - Medical Education
12. IMAGE + TITLE - Minimally Invasive Technology
13. IMAGE + TEXT - Minimally Invasive Technology
14. IMAGE + TITLE - Impact Phrase
15. IMAGE + TEXT - Impact Phrase
16. Back

As longs as the text is under development and will be placed internally in the winning design, please use 'lorem ipsum' for text areas. The titles can follow the index above.

Nice to have
• The use of office pictures with some style / artistic finish in pages "about us"

```html
<!DOCTYPE html>
<html lang="en">
<head>
<meta charset="UTF-8">
<title>Corvalento Brochure – Spread</title>
<link rel="stylesheet" href="https://fonts.googleapis.com/css2?family=Poppins:wght@600&family=Questrial&display=swap">
<style>
  :root {
    --brand-green: #27924f;
    --ink-grey: #58595b;
    --paper: #ffffff;
    --photo-equipment: linear-gradient(160deg, #e9eef1 0%, #c9d3d8 45%, #8f9ea6 100%);
    --photo-surgery: linear-gradient(170deg, #7fc79a 0%, #3f9f63 55%, #2c7f4c 100%);
    --photo-office: linear-gradient(150deg, #e6e2d8 0%, #c9b89a 50%, #6d5c48 100%);
  }
  * { margin: 0; padding: 0; box-sizing: border-box; }
  html, body { width: 1200px; height: 848px; overflow: hidden; background: var(--paper); }
  .spread {
    position: relative;
    width: 1200px;
    height: 848px;
    background: var(--paper);
    font-family: "Questrial", "Century Gothic", sans-serif;
    overflow: hidden;
  }
  .photo { position: absolute; }
  .photo--equipment { left: 0; top: 0; width: 398px; height: 282px; background: var(--photo-equipment); }
  .photo--surgery { left: 0; top: 286px; width: 398px; height: 562px; background: var(--photo-surgery); }
  .photo--office { left: 808px; top: 581px; width: 392px; height: 267px; background: var(--photo-office); }

  .headline {
    position: absolute;
    left: 412px;
    top: 124px;
    font-family: "Poppins", "Century Gothic", sans-serif;
    font-weight: 600;
    font-size: 58px;
    line-height: 60px;
    letter-spacing: -0.5px;
    white-space: nowrap;
  }
  .headline__lead { display: block; color: var(--brand-green); }
  .headline__tail { display: block; color: var(--ink-grey); }

  .section-title {
    font-family: "Poppins", "Century Gothic", sans-serif;
    font-weight: 600;
    font-size: 32px;
    line-height: 40px;
    white-space: nowrap;
  }
  .body-copy {
    font-size: 16.2px;
    line-height: 26.6px;
    white-space: nowrap;
  }

  .feature-panel {
    position: absolute;
    left: 405px;
    top: 285px;
    width: 795px;
    height: 282px;
    background: var(--brand-green);
    padding: 22px 20px 0 28px;
    color: var(--paper);
  }
  .feature-panel .body-copy { margin-top: 14px; }

  .side-column {
    position: absolute;
    left: 433px;
    top: 582px;
    width: 360px;
    height: 266px;
    color: var(--brand-green);
  }
  .side-column .body-copy { margin-top: 12px; }
</style>
</head>
<body>
  <main class="spread">
    <div class="photo photo--equipment" role="img" aria-label="Photo of medical imaging equipment on display in an exhibition hall"></div>
    <div class="photo photo--surgery" role="img" aria-label="Green-toned photo of a surgical team operating under theatre lights"></div>
    <div class="photo photo--office" role="img" aria-label="Photo of a meeting room with a round table, chairs and a wall screen"></div>

    <h1 class="headline">
      <span class="headline__lead">here is no one who</span>
      <span class="headline__tail">loves pain itself,</span>
    </h1>

    <section class="feature-panel">
      <h2 class="section-title">because it is pain..."</h2>
      <p class="body-copy">Lorem Ipsum is simply dummy text of the printing and typesetting industry. Lorem Ipsum has<br>
      been the industry's standard dummy text ever since the 1500s, when an unknown printer took<br>
      a galley of type and scrambled it to make a type specimen book. It has survived not only five<br>
      centuries, but also the leap into electronic typesetting, remaining essentially unchanged. It<br>
      was popularised in the 1960s with the release of Quillmark sheets containing Lorem Ipsum<br>
      passages, and more recently with desktop publishing software like Pagewright including<br>
      versions of Lorem Ipsum.</p>
    </section>

    <section class="side-column">
      <h2 class="section-title">because it is pain..."</h2>
      <p class="body-copy">Lorem Ipsum is simply dummy text of the<br>
      printing and typesetting industry. Lorem<br>
      Ipsum has been the industry's standard<br>
      dummy text ever since the 1500s, when an<br>
      unknown printer took a galley of type and<br>
      scrambled it to make a type specimen<br>
      book. It has survived not only five centuries,</p>
    </section>
  </main>
</body>
</html>
```